Real Estate Brokerage Stationery Designs

I am looking to have presentation folders with business card slots on both sides along with pockets on both sides. I've attached logos, website colors along with current business card designs.

I am looking for envelope designs both big and small. Possibly new business card designs, notepad templates for big and small notepads. Letterhead designs. Pop socket designs. Realtors name badge designs.

www.brightholdrealty.example

```html
<!DOCTYPE html>
<html lang="en">
<head>
<meta charset="utf-8">
<title>Brighthold Realty – Stationery Set</title>
<link href="https://fonts.googleapis.com/css2?family=Roboto:wght@400;500&family=Source+Sans+3:wght@400;600&display=swap" rel="stylesheet">
<style>
:root{
  --stage:#a8a6a7;
  --paper:#f4f3f1;
  --brand:#0a4fa6;
  --ink:#3a3a3a;
  --muted:#6a6a6a;
  --rule:#9a9a9a;
  --white:#ffffff;
}
*{box-sizing:border-box;margin:0;padding:0}
html,body{width:1074px;height:1200px;overflow:hidden;background:var(--stage)}
body{position:relative;font-family:"Source Sans 3",sans-serif;color:var(--ink)}
.sheet{position:absolute;background:var(--paper);overflow:hidden}

.brand-name{display:flex;align-items:center;gap:6px;font-family:"Source Sans 3",sans-serif;font-weight:600;color:var(--brand);white-space:nowrap}
.brand-name .mark{display:inline-block;background:var(--brand)}
.brand-name.on-blue{color:var(--white)}
.brand-name.on-blue .mark{background:var(--white)}

.band{position:absolute;left:0;right:0;background:var(--brand);color:var(--white);font-family:"Roboto",sans-serif}
.band .url{display:block;text-align:left;letter-spacing:2.4px}

/* Letterhead */
.letterhead{left:54px;top:31px;width:439px;height:618px}
.letterhead .brand-name{position:absolute;top:90px;left:0;right:0;justify-content:center;font-size:20px}
.letterhead .brand-name .mark{width:14px;height:14px}
.letter-body{position:absolute;left:45px;top:173px;width:355px}
.salutation{font-size:12px;color:var(--ink);margin-bottom:20px}
.letter-body p{font-size:6.2px;line-height:10.4px;color:var(--muted);margin-bottom:10px;text-align:justify}
.signoff{position:absolute;left:45px;top:432px;font-size:6.4px;color:var(--muted)}
.signer{position:absolute;left:46px;top:478px;font-size:6.6px;line-height:10.4px;color:var(--muted)}
.letterhead .band{top:544px;height:59px;font-size:7.6px;line-height:10.4px;padding:8px 40px 0 50px;display:flex;justify-content:space-between}
.contact-list{list-style:none}
.contact-list li{display:flex;align-items:center;gap:5px}
.contact-list svg{width:7px;height:7px;fill:var(--white)}
.address{text-align:right}

/* DL envelope front */
.env-front{left:526px;top:169px;width:491px;height:224px}
.env-front .flap{position:absolute;left:0;top:0;width:491px;height:82px}
.env-front .brand-name{position:absolute;top:40px;left:0;right:0;justify-content:center;font-size:14px}
.env-front .brand-name .mark{width:10px;height:10px}

/* DL envelope back */
.env-back{left:527px;top:425px;width:493px;height:223px}
.env-back .brand-name{position:absolute;left:20px;top:52px;font-size:16px}
.env-back .brand-name .mark{width:12px;height:12px}
.env-back .return-address{position:absolute;left:19px;top:104px;font-family:"Roboto",sans-serif;font-size:7.4px;line-height:10px;color:var(--muted)}
.env-back .band{top:192px;height:18px;font-size:7px;padding:4px 0 0 27px}

/* A4 envelope */
.env-a4{left:38px;top:726px;width:282px;height:435px}
.env-a4 .flap{position:absolute;left:0;top:0;width:282px;height:36px}
.env-a4 .flap-name{position:absolute;top:13px;left:0;right:0;justify-content:center;font-size:9px}
.env-a4 .flap-name .mark{width:7px;height:7px}
.env-a4 .corner-name{position:absolute;left:12px;top:60px;font-size:11px}
.env-a4 .corner-name .mark{width:8px;height:8px}
.env-a4 .return-address{position:absolute;left:12px;top:108px;font-family:"Roboto",sans-serif;font-size:5.6px;line-height:7.4px;color:var(--muted)}
.env-a4 .band{top:414px;height:13px;font-size:6.4px;padding:1.5px 0 0 84px}
.caption{position:absolute;left:38px;width:282px;top:1168px;text-align:center;font-family:"Source Sans 3",sans-serif;font-weight:600;font-size:11px;color:#111}

/* Notepads */
.notepad-large{left:357px;top:718px;width:346px;height:448px}
.notepad-large .brand-name{position:absolute;top:60px;left:0;right:0;justify-content:center;font-size:12px}
.notepad-large .brand-name .mark{width:9px;height:9px}
.notepad-large .band{top:426px;height:13px;font-size:6.4px;padding:1.5px 0 0 110px}
.writing-lines{position:absolute;left:26px;width:289px}
.writing-lines span{display:block;height:1px;background:var(--rule);opacity:.7}
.notepad-large .writing-lines{top:95px}
.notepad-large .writing-lines span{margin-bottom:18.6px}

.tent-card{left:745px;top:718px;width:268px;height:194px;background:linear-gradient(90deg,#e9e7e3,#f6f5f2 60%,#e6e4e0)}
.tent-card .brand-name{position:absolute;top:88px;left:0;right:0;justify-content:center;font-size:17px}
.tent-card .brand-name .mark{width:12px;height:12px}

.notepad-small{left:746px;top:972px;width:268px;height:194px}
.notepad-small .brand-name{position:absolute;top:42px;left:0;right:0;justify-content:center;font-size:10px}
.notepad-small .brand-name .mark{width:7px;height:7px}
.notepad-small .writing-lines{top:72px;left:28px;width:219px}
.notepad-small .writing-lines span{margin-bottom:17.6px}
.notepad-small .band{top:174px;height:13px;font-size:6.4px;padding:1.5px 0 0 78px}
</style>
</head>
<body>

<section class="sheet letterhead" aria-label="Letterhead">
  <div class="brand-name"><span class="mark"></span>Brighthold Realty</div>
  <div class="letter-body">
    <p class="salutation">Dear Mr. Carter,</p>
    <p>Thank you for considering our team for your next move. We have reviewed the details you shared and prepared a short outline of the homes and listings that match your goals. Our agents know the local market well and will guide each step with care, from first viewing through the closing table and beyond.</p>
    <p>We will arrange tours at times that suit you and keep you informed of new listings as they arrive. Pricing, inspection and financing questions can be handled by our office staff, who are ready to help whenever you need them.</p>
    <p>Please find attached a summary of recent sales in the area along with our suggested timeline. Should any part of the plan need changes, let us know and we will adjust it promptly to fit your needs.</p>
    <p>We look forward to working with you and helping you find the right place to call home.</p>
  </div>
  <p class="signoff">Sincerely,</p>
  <p class="signer">Alex Morgan<br>CEO/ Founder</p>
  <div class="band">
    <ul class="contact-list">
      <li><svg viewBox="0 0 10 10"><path d="M2 0l2 2.5-1 1.2c.6 1.3 1.6 2.3 2.9 2.9l1.2-1L10 8 8.5 10C4 9.6.4 6 0 1.5z"/></svg>555-010-2210</li>
      <li><svg viewBox="0 0 10 10"><path d="M2.5 0h5v10h-5zM3.5 1v7h3V1z"/></svg>555-010-3342</li>
      <li><svg viewBox="0 0 10 10"><path d="M2.5 0h5v3h-5zM0 3.5h10v4H8V10H2V7.5H0z"/></svg>555-010-4478</li>
      <li><svg viewBox="0 0 10 10"><path d="M0 2h10v6H0zM1 3l4 3 4-3"/></svg>hello@brightholdrealty.example</li>
    </ul>
    <div class="address">240 Harbor Lane<br>Suite 12<br>Lakeview, FL 30100<br><span style="letter-spacing:.8px">www.brightholdrealty.example</span></div>
  </div>
</section>

<section class="sheet env-front" aria-label="Envelope front">
  <svg class="flap" viewBox="0 0 491 82" aria-hidden="true"><path d="M0 0H491L484 50Q480 82 448 82H42Q10 82 7 50Z" fill="var(--brand)"/></svg>
  <div class="brand-name on-blue"><span class="mark"></span>Brighthold Realty</div>
</section>

<section class="sheet env-back" aria-label="Envelope with return address">
  <div class="brand-name"><span class="mark"></span>Brighthold Realty</div>
  <p class="return-address">240 Harbor Lane, Suite 12,<br>Lakeview, FL 30100</p>
  <div class="band"><span class="url">www.brightholdrealty.example</span></div>
</section>

<section class="sheet env-a4" aria-label="Envelope A4">
  <svg class="flap" viewBox="0 0 282 36" aria-hidden="true"><path d="M0 36L4 14Q7 0 22 0H260Q275 0 278 14L282 36Z" fill="var(--brand)"/></svg>
  <div class="brand-name on-blue flap-name"><span class="mark"></span>Brighthold Realty</div>
  <div class="brand-name corner-name"><span class="mark"></span>Brighthold Realty</div>
  <p class="return-address">240 Harbor Lane, Suite 12,<br>Lakeview, FL 30100</p>
  <div class="band"><span class="url">www.brightholdrealty.example</span></div>
</section>
<p class="caption">Envelope A4</p>

<section class="sheet notepad-large" aria-label="Large notepad">
  <div class="brand-name"><span class="mark"></span>Brighthold Realty</div>
  <div class="writing-lines"><span></span><span></span><span></span><span></span><span></span><span></span><span></span><span></span><span></span><span></span><span></span><span></span><span></span><span></span><span></span><span></span><span></span></div>
  <div class="band"><span class="url">www.brightholdrealty.example</span></div>
</section>

<section class="sheet tent-card" aria-label="Tent card">
  <div class="brand-name"><span class="mark"></span>Brighthold Realty</div>
</section>

<section class="sheet notepad-small" aria-label="Small notepad">
  <div class="brand-name"><span class="mark"></span>Brighthold Realty</div>
  <div class="writing-lines"><span></span><span></span><span></span><span></span><span></span></div>
  <div class="band"><span class="url">www.brightholdrealty.example</span></div>
</section>

</body>
</html>
```